A new presentation to our clients

we are a Real Estate agency, our website is www.lumibrasa.com and it’s time to have a new, fashion and remarcable Business Card. we want to differentiate ourselves from other companies so we want a business card that differentiates us. we want the business card to impact our customers. in the competitive market that we have today, we have to be different and it is this difference that we seek

Target Market(s)

Real Estate Clients

Contact Information for Business Card

We search a totaly diferent card from the usual

Font styles to use
Sans Serif

Colors
e34197

Requirements
Must have
• Logo, adress, phone contact, e-mail, photo, and our website
Nice to have
• We would like to see a modern business card
Should not have
• Houses or building draws

```html
<!DOCTYPE html>
<html lang="pt">
<head>
<meta charset="utf-8">
<title>Lumibrasa — Business Card</title>
<link rel="stylesheet" href="https://fonts.googleapis.com/css2?family=Roboto:wght@400;500;700&display=swap">
<style>
  :root {
    --brand: #e0337f;
    --brand-deep: #b4155a;
    --brand-line: #ec5a9c;
    --ink: #4a4a4a;
    --ink-soft: #666666;
    --card-white: #ffffff;
    --card-shade: #ececec;
    --logo-silver: #cfcfcf;
    --stage: #3a3a3a;
  }
  * { box-sizing: border-box; margin: 0; padding: 0; }
  html, body { width: 1200px; height: 900px; overflow: hidden; }
  body {
    background: var(--stage);
    font-family: "Roboto", Arial, sans-serif;
    position: relative;
  }
  .card {
    position: absolute;
    left: 285px;
    width: 630px;
    height: 360px;
    border-radius: 22px;
    overflow: hidden;
  }
  .card--front {
    top: 70px;
    background: linear-gradient(135deg, var(--card-shade) 0%, var(--card-white) 55%, var(--card-white) 100%);
  }
  .card--back {
    top: 470px;
    background: linear-gradient(135deg, var(--brand) 0%, var(--brand-deep) 100%);
    display: flex;
    align-items: center;
    justify-content: center;
  }
  .holder { position: absolute; left: 44px; top: 52px; }
  .holder__name {
    color: var(--brand);
    font-size: 25px;
    font-weight: 500;
    letter-spacing: 0.5px;
    text-transform: uppercase;
  }
  .holder__role {
    color: var(--ink-soft);
    font-size: 17px;
    margin-top: 2px;
  }
  .divider {
    position: absolute;
    left: 140px;
    top: 109px;
    width: 410px;
    height: 2px;
    background: var(--brand-line);
  }
  .brand-name {
    position: absolute;
    right: 60px;
    top: 40px;
    color: var(--brand);
    font-size: 44px;
    font-weight: 700;
    letter-spacing: 0.5px;
  }
  .contacts {
    position: absolute;
    left: 30px;
    top: 130px;
    list-style: none;
  }
  .contacts li {
    display: flex;
    align-items: center;
    gap: 8px;
    color: var(--ink);
    font-size: 17px;
    line-height: 26px;
  }
  .contacts svg { width: 11px; height: 11px; fill: var(--brand); flex: none; }
  .address {
    position: absolute;
    right: 70px;
    bottom: 60px;
    color: var(--ink);
    font-size: 17px;
    line-height: 25px;
  }
  .brand-name--back {
    color: var(--logo-silver);
    font-size: 92px;
    font-weight: 700;
    letter-spacing: 1px;
  }
</style>
</head>
<body>
  <section class="card card--front">
    <div class="holder">
      <p class="holder__name">Daniel Ferreira</p>
      <p class="holder__role">Director</p>
    </div>
    <div class="divider"></div>
    <p class="brand-name">Lumibrasa</p>
    <ul class="contacts">
      <li>
        <svg viewBox="0 0 12 12" aria-hidden="true"><path d="M2.5 0.5 L4.5 3 L3.5 4.5 C4.2 6 6 7.8 7.5 8.5 L9 7.5 L11.5 9.5 L10 11.5 C5 11 1 7 0.5 2 Z"/></svg>
        (+351) 224 618 305
      </li>
      <li>
        <svg viewBox="0 0 12 12" aria-hidden="true"><rect x="3" y="0.5" width="6" height="3"/><rect x="0.5" y="4" width="11" height="5" rx="1"/><rect x="3" y="8" width="6" height="3.5"/></svg>
        (+351) 224 618 309
      </li>
      <li>
        <svg viewBox="0 0 12 12" aria-hidden="true"><path d="M0.5 2 H11.5 V10 H0.5 Z M1.5 3 L6 6.5 L10.5 3 V3.2 L6 7.5 L1.5 3.2 Z" fill-rule="evenodd"/></svg>
        geral@lumibrasa.com
      </li>
      <li>
        <svg viewBox="0 0 12 12" aria-hidden="true"><circle cx="6" cy="6" r="5.5"/></svg>
        www.lumibrasa.com
      </li>
    </ul>
    <address class="address" style="font-style: normal;">
      Rua das Camélias, 148<br>
      4410-052, Vila Nova de Gaia
    </address>
  </section>

  <section class="card card--back">
    <p class="brand-name--back">Lumibrasa</p>
  </section>
</body>
</html>
```